CREATE A BUSINESS CARD FOR A BOAT CLEANING SERVICE

WE ARE STARTING A NEW BOAT CLEANING BUSINESS. WE DIVE UNDERWATER TO CLEAN BOAT HULLS, JETTIES, UNDERWATER STRUCTURES ETC. WE ARE LOOKING FOR AN UPPERMARKET MODERN LOGO AND BUSINESS CARD AS ALOT OF OUR TARGET MARKET WILL BE HIGH END. YOU HAVE TO DESIGN A BUSINESS CARD AND LOGO SEPERATELY .
THE BUSINESS CARD DIMESNION MUST BE STANDARD SIZE.
The standard dimensions of a printed business card are 3.5 x 2 inches

Target Market(s)

UNDERWATER SERVICED

Industry/Entity Type

Business

Contact Information for Business Card

HOLLAND UNDERWATER SERVICES

Font styles to use
Serif

Colors

Designer to choose colors to be used in the design.

Requirements
Must have
• HOLLAND
Nice to have
• dark
Should not have
• more than 3 colors

```html
<!DOCTYPE html>
<html lang="en">
<head>
<meta charset="utf-8">
<title>Holland Underwater Services – Business Card</title>
<link rel="stylesheet" href="https://fonts.googleapis.com/css2?family=Cinzel:wght@400;600&family=Lato:wght@400&display=swap">
<style>
  :root {
    --backdrop: #3b3431;
    --card: #0d0d0e;
    --blue: #2f6fb8;
    --silver: #b9bcc0;
    --white: #e9eaec;
    --rule: #55585c;
  }
  * { margin: 0; padding: 0; box-sizing: border-box; }
  html, body { width: 1200px; height: 900px; overflow: hidden; }
  body {
    background: var(--backdrop);
    display: flex;
    align-items: center;
    justify-content: center;
    gap: 60px;
    font-family: "Lato", Arial, sans-serif;
  }
  .card {
    width: 525px;
    height: 300px;
    background: var(--card);
    position: relative;
    box-shadow: 0 14px 30px rgba(0,0,0,.45);
  }
  /* Front */
  .card-front { display: flex; align-items: center; }
  .brand-block {
    width: 260px;
    padding-left: 34px;
    display: flex;
    align-items: center;
    gap: 12px;
  }
  .brand-dot {
    width: 14px; height: 14px; border-radius: 50%;
    background: var(--blue); flex: none;
  }
  .brand-name {
    font-family: "Cinzel", Georgia, serif;
    font-weight: 600;
    color: var(--blue);
    font-size: 19px;
    line-height: 1.25;
    letter-spacing: 1px;
  }
  .divider {
    width: 1px; height: 180px;
    background: linear-gradient(transparent, var(--rule), transparent);
  }
  .contact-block { padding-left: 26px; color: var(--white); }
  .person-name {
    font-family: "Cinzel", Georgia, serif;
    color: var(--blue);
    font-size: 19px;
    letter-spacing: 1px;
  }
  .person-role { font-size: 14px; margin-bottom: 14px; }
  .contact-list { list-style: none; font-size: 14px; line-height: 1.6; }
  .contact-list li { display: flex; align-items: center; gap: 8px; }
  .contact-list svg { width: 11px; height: 11px; fill: var(--silver); flex: none; }
  .address { font-size: 14px; line-height: 1.4; margin-top: 12px; }
  /* Back */
  .card-back {
    display: flex; flex-direction: column;
    align-items: center; justify-content: center;
    text-align: center;
  }
  .back-brand {
    font-family: "Cinzel", Georgia, serif;
    font-weight: 600;
    color: var(--silver);
    font-size: 26px;
    letter-spacing: 2px;
    line-height: 1.3;
  }
  .tagline {
    margin-top: 40px;
    font-family: "Cinzel", Georgia, serif;
    color: var(--silver);
    font-size: 11px;
    letter-spacing: .5px;
    line-height: 1.5;
  }
</style>
</head>
<body>
  <section class="card card-front" aria-label="Business card front">
    <div class="brand-block">
      <span class="brand-dot"></span>
      <div class="brand-name">HOLLAND<br>UNDERWATER SERVICES</div>
    </div>
    <div class="divider"></div>
    <div class="contact-block">
      <div class="person-name">MARCUS REED</div>
      <div class="person-role">Managing Director</div>
      <ul class="contact-list">
        <li><svg viewBox="0 0 12 12"><path d="M2 1h3l1 3-2 1a7 7 0 0 0 3 3l1-2 3 1v3c-6 0-10-4-10-10z"/></svg>444 555 0192</li>
        <li><svg viewBox="0 0 12 12"><path d="M0 2h12v8H0z M1 3l5 4 5-4" stroke="#0d0d0e" stroke-width="1"/></svg>hello@hollanddive.com</li>
        <li><svg viewBox="0 0 12 12"><circle cx="6" cy="6" r="6"/></svg>www.hollanddive.com</li>
      </ul>
      <div class="address">17 Harbour Road,<br>Seaport, 45120</div>
    </div>
  </section>

  <section class="card card-back" aria-label="Business card back">
    <div class="back-brand">HOLLAND<br>UNDERWATER SERVICES</div>
    <p class="tagline">WE DIVE UNDERWATER TO CLEAN BOAT HULLS, JETTIES,<br>UNDERWATER STRUCTURES ETC</p>
  </section>
</body>
</html>
```